German Headhunter/ HR Consultancy needs Business Cards Design

We need a business Card Design for our Company in Stuttgart. We are specialized as Headhunter/ HR Consultancy in Placement of specialist and managers in permanent employment. Please refer to our business logo.

```html
<!DOCTYPE html>
<html lang="de">
<head>
<meta charset="utf-8">
<title>Kestrel Personalberatung – Visitenkarte</title>
<link href="https://fonts.googleapis.com/css2?family=Montserrat:wght@600;800&family=Arimo:wght@400&display=swap" rel="stylesheet">
<style>
  :root {
    --stage: #2b2b2d;
    --card: #ffffff;
    --brand-blue: #3a55a6;
    --brand-blue-light: #5067b3;
    --brand-grey: #97989b;
    --ink-light: #ffffff;
  }
  html, body {
    margin: 0;
    width: 1200px;
    height: 900px;
    overflow: hidden;
    background: var(--stage);
  }
  .stage {
    position: relative;
    width: 1200px;
    height: 900px;
  }
  .card {
    position: absolute;
    left: 250px;
    width: 700px;
    height: 400px;
    border-radius: 24px;
    overflow: hidden;
    box-shadow: 0 14px 32px rgba(0,0,0,.45);
  }
  .card--front { top: 30px; background: var(--card); }
  .card--back { top: 470px; background: var(--brand-blue); }

  .card__bands { position: absolute; inset: 0; }

  .brand {
    position: absolute;
    display: flex;
    align-items: center;
    gap: 13px;
  }
  .brand__square {
    width: 45px;
    height: 45px;
    background: var(--brand-blue);
    flex: none;
  }
  .brand__name {
    font-family: "Montserrat", sans-serif;
    font-weight: 800;
    font-size: 27px;
    letter-spacing: .3px;
    color: var(--brand-blue);
    line-height: 1;
    white-space: nowrap;
  }
  .brand--front { left: 210px; top: 64px; }
  .brand--back { left: 56px; bottom: 58px; }
  .brand--back .brand__square { background: var(--ink-light); }
  .brand--back .brand__name { color: var(--ink-light); }

  .brand-square-large {
    position: absolute;
    left: 532px;
    top: 183px;
    width: 119px;
    height: 119px;
    background: var(--ink-light);
  }

  .contact {
    position: absolute;
    left: 56px;
    top: 176px;
    color: var(--ink-light);
  }
  .contact__name {
    margin: 0;
    font-family: "Montserrat", sans-serif;
    font-weight: 800;
    font-size: 27px;
    letter-spacing: .8px;
    text-transform: uppercase;
    line-height: 1.1;
  }
  .contact__role {
    margin: 2px 0 16px;
    font-family: "Arimo", sans-serif;
    font-size: 16px;
  }
  .contact__list {
    list-style: none;
    margin: 0;
    padding: 0;
    font-family: "Arimo", sans-serif;
    font-size: 16px;
  }
  .contact__item {
    display: flex;
    align-items: center;
    gap: 9px;
    margin-bottom: 8px;
  }
  .contact__icon { width: 13px; height: 13px; flex: none; }

  .back-pattern {
    position: absolute;
    inset: 0;
    background: linear-gradient(120deg, var(--brand-blue) 0%, var(--brand-blue) 55%, var(--brand-blue-light) 100%);
  }
</style>
</head>
<body>
<main class="stage">
  <article class="card card--front">
    <svg class="card__bands" viewBox="0 0 700 400" width="700" height="400" aria-hidden="true">
      <polygon points="0,160 574,160 462,352 0,352" fill="var(--brand-blue)"/>
      <polygon points="574,160 700,160 700,352 462,352" fill="var(--brand-grey)"/>
    </svg>

    <div class="brand brand--front">
      <span class="brand__square"></span>
      <span class="brand__name">Kestrel Personalberatung</span>
    </div>

    <span class="brand-square-large"></span>

    <section class="contact">
      <h1 class="contact__name">Jonas Weber</h1>
      <p class="contact__role">CEO/Founder</p>
      <ul class="contact__list">
        <li class="contact__item">
          <svg class="contact__icon" viewBox="0 0 24 24" fill="currentColor"><path d="M6.6 10.8a15.1 15.1 0 0 0 6.6 6.6l2.2-2.2a1 1 0 0 1 1-.25 11.4 11.4 0 0 0 3.6.57 1 1 0 0 1 1 1V20a1 1 0 0 1-1 1A17 17 0 0 1 3 4a1 1 0 0 1 1-1h3.5a1 1 0 0 1 1 1c0 1.25.2 2.45.57 3.6a1 1 0 0 1-.25 1z"/></svg>
          <span>(555) 014 - 2280</span>
        </li>
        <li class="contact__item">
          <svg class="contact__icon" viewBox="0 0 24 24" fill="currentColor"><path d="M2 5h20v14H2zm2 2v.5l8 5 8-5V7zm0 2.9V17h16V9.9l-8 5z"/></svg>
          <span>info@kestrelpersonal.com</span>
        </li>
        <li class="contact__item">
          <svg class="contact__icon" viewBox="0 0 24 24" fill="none" stroke="currentColor" stroke-width="2"><circle cx="12" cy="12" r="9"/><path d="M3 12h18M12 3c3 3.5 3 14.5 0 18M12 3c-3 3.5-3 14.5 0 18"/></svg>
          <span>www.kestrelpersonal.com</span>
        </li>
      </ul>
    </section>
  </article>

  <article class="card card--back">
    <div class="back-pattern" role="img" aria-label="Repeating brand monogram pattern in tonal blue, fading to white toward the upper right"></div>
    <div class="brand brand--back">
      <span class="brand__square"></span>
      <span class="brand__name">Kestrel Personalberatung</span>
    </div>
  </article>
</main>
</body>
</html>
```